Business card design needed

I would like a one sided black business card with the information provided above. Refer to my website www.brightvolleyracquets.com.au for an example of colors I have used for my site, would like to keep this consistent for my business cards also, I will upload my logo below.

I am a new small business that provides tennis customers with racquet re stringing, tennis strings and accessories.

Industry/Entity Type

Small Business

Contact Information for Business Card

Bright Volley Tennis

Owen Whitby
Managing Director

brightvolleyracquets@mailbox.example
www.brightvolleyracquets.com.au
0491 726 305

Racquet Restringing/Tennis Strings/Accessories

Requirements
Must have
• Must have my logo and card must be black

```html
<!DOCTYPE html>
<html lang="en">
<head>
<meta charset="utf-8">
<title>Bright Volley Tennis – Business Card</title>
<link href="https://fonts.googleapis.com/css2?family=Open+Sans:wght@400;600;800&display=swap" rel="stylesheet">
<style>
  :root {
    --backdrop: #e6e4e1;
    --card-black: #000000;
    --lime: #b7d433;
    --steel-blue: #5a77b9;
    --navy: #28407a;
    --white: #ffffff;
    --ink: #1a1a1a;
  }
  * { box-sizing: border-box; margin: 0; padding: 0; }
  html, body {
    width: 1200px; height: 475px; overflow: hidden;
    background: var(--backdrop);
    font-family: "Open Sans", Arial, sans-serif;
  }
  .canvas { position: relative; width: 1200px; height: 475px; }

  .card {
    position: absolute;
    background: var(--card-black);
    border-radius: 15px;
    overflow: hidden;
  }
  .card--front { left: 23px; top: 80px; width: 547px; height: 315px; }
  .card--back  { left: 607px; top: 85px; width: 546px; height: 311px; }

  .brand {
    position: absolute;
    display: flex; align-items: center; gap: 9px;
    color: var(--lime);
    font-weight: 800;
    text-transform: uppercase;
    line-height: 1.05;
  }
  .brand__dot { flex: none; border-radius: 50%; background: var(--lime); }
  .card--front .brand { left: 30px; top: 82px; width: 235px; font-size: 22px; }
  .card--front .brand__dot { width: 38px; height: 38px; }
  .card--back .brand { left: 50%; top: 108px; transform: translateX(-50%); width: 360px; font-size: 31px; justify-content: center; }
  .card--back .brand__dot { width: 50px; height: 50px; }

  .contact-list {
    position: absolute; left: 276px; top: 100px;
    list-style: none; color: var(--white);
    font-size: 12px; letter-spacing: -0.1px; white-space: nowrap;
  }
  .contact-list li { display: flex; align-items: center; height: 20px; }
  .contact-list svg { width: 11px; height: 11px; margin-right: 8px; fill: var(--lime); flex: none; }

  .wave { position: absolute; left: 0; top: 0; width: 100%; height: 100%; }

  .holder { position: absolute; left: 316px; top: 238px; color: var(--ink); }
  .holder__name { font-size: 18px; font-weight: 400; text-transform: uppercase; letter-spacing: 0.2px; }
  .holder__role { font-size: 13px; margin-top: 1px; }

  .web-line {
    position: absolute; left: 0; right: 0; top: 240px;
    text-align: center; color: var(--white);
    font-size: 13.5px; letter-spacing: 2.4px; white-space: nowrap;
  }
</style>
</head>
<body>
<div class="canvas">

  <section class="card card--front" aria-label="Business card front">
    <svg class="wave" viewBox="0 0 525 302" preserveAspectRatio="none" aria-hidden="true">
      <path d="M0 196 C60 230 110 262 190 262 C300 262 380 190 525 186 L525 302 L0 302 Z" fill="var(--lime)"/>
      <path d="M0 196 C60 222 120 246 200 244 C300 240 390 186 525 178 L525 192 C400 196 310 254 200 258 C120 260 55 236 0 206 Z" fill="var(--card-black)"/>
      <path d="M18 212 C90 250 150 258 220 248 C320 232 400 188 525 180 L525 186 C410 196 330 244 220 256 C150 262 80 250 18 212 Z" fill="var(--steel-blue)"/>
      <path d="M60 220 C130 250 200 246 280 226 C360 206 430 192 525 190 L525 194 C440 198 370 214 290 232 C200 252 130 254 60 220 Z" fill="var(--navy)"/>
    </svg>

    <div class="brand"><span class="brand__dot"></span><span>Bright Volley Tennis</span></div>

    <ul class="contact-list">
      <li><svg viewBox="0 0 24 24"><path d="M6.6 10.8a15.1 15.1 0 0 0 6.6 6.6l2.2-2.2a1 1 0 0 1 1-.25 11.4 11.4 0 0 0 3.6.57 1 1 0 0 1 1 1V20a1 1 0 0 1-1 1A17 17 0 0 1 3 4a1 1 0 0 1 1-1h3.5a1 1 0 0 1 1 1c0 1.25.2 2.45.57 3.57a1 1 0 0 1-.25 1z"/></svg>0491 726 305</li>
      <li><svg viewBox="0 0 24 24"><path d="M2 6h20v12H2z M2 6l10 7 10-7" stroke="var(--card-black)" stroke-width="1.5"/></svg>brightvolleyracquets@mailbox.example</li>
      <li><svg viewBox="0 0 24 24"><circle cx="12" cy="12" r="10"/><path d="M2 12h20M12 2c3 3 3 17 0 20M12 2c-3 3-3 17 0 20" stroke="var(--card-black)" stroke-width="1.6" fill="none"/></svg>www.brightvolleyracquets.com.au</li>
    </ul>

    <div class="holder">
      <p class="holder__name">Owen Whitby</p>
      <p class="holder__role">Managing Director</p>
    </div>
  </section>

  <section class="card card--back" aria-label="Business card back">
    <div class="brand"><span class="brand__dot"></span><span>Bright Volley Tennis</span></div>
    <p class="web-line">www.brightvolleyracquets.com.au</p>
  </section>

</div>
</body>
</html>
```